VFX Company Business Card Design Project

The Kestrel Works is a decentralized Visual Effects Studio servicing the television and feature film industries.
Project Brief:
Take our logo that was previously designed on Pencil Harbor and make a double sided business card.
Requirements:
- Card MUST be double sided.
- Front of card MUST have the yellow part of our logo against the dark grey background.
- Back of card is completely up to the designer.
- Back of card must include the complete company logo.
Please follow these File Preparation guidelines:
http://printnook.ca/infopage?file=filetype_en&s=PrintNook_new&lang=en
Business

```html
<!DOCTYPE html>
<html lang="en">
<head>
<meta charset="utf-8">
<title>The Kestrel Works – Business Cards</title>
<link rel="stylesheet" href="https://fonts.googleapis.com/css2?family=Arimo:wght@400;700&family=Jost:wght@400;500&display=swap">
<style>
  :root {
    --backdrop: #e4e2de;
    --card: #2b2b2b;
    --gold: #fdc42d;
    --slate: #5f6569;
    --paper: #eef0e8;
    --ink-light: #ffffff;
  }
  * { margin: 0; padding: 0; box-sizing: border-box; }
  html, body { width: 1200px; height: 734px; overflow: hidden; }
  body { background: var(--backdrop); position: relative; font-family: "Arimo", Arial, sans-serif; }

  .card {
    position: absolute;
    width: 524px;
    height: 300px;
    background: var(--card);
    color: var(--ink-light);
  }
  .card--front   { left: 67px;  top: 43px; }
  .card--contact { left: 628px; top: 48px; }
  .card--brand   { left: 63px;  top: 381px; }
  .card--word    { left: 622px; top: 387px; }

  .wordmark {
    position: absolute;
    font-family: "Jost", Arial, sans-serif;
    font-weight: 500;
    white-space: nowrap;
    display: flex;
    align-items: center;
  }
  .wordmark__dot {
    display: inline-block;
    border-radius: 50%;
    background: currentColor;
  }
  .wordmark--hero { color: var(--gold); font-size: 52px; left: 0; right: 0; top: 112px; justify-content: center; gap: 18px; }
  .wordmark--hero .wordmark__dot { width: 34px; height: 34px; }
  .wordmark--header { color: var(--paper); font-size: 38px; left: 40px; right: 40px; top: 82px; justify-content: center; gap: 14px; }
  .wordmark--header .wordmark__dot { width: 24px; height: 24px; color: var(--gold); background: var(--gold); }
  .wordmark--mid { color: var(--paper); font-size: 40px; left: 36px; right: 36px; top: 106px; justify-content: center; gap: 14px; }
  .wordmark--mid .wordmark__dot { width: 26px; height: 26px; background: var(--gold); }
  .wordmark--large { color: var(--paper); font-size: 50px; left: 0; right: 0; top: 98px; justify-content: center; }

  .web {
    position: absolute;
    left: 0; right: 0;
    bottom: 24px;
    text-align: center;
    font-family: "Jost", Arial, sans-serif;
    font-size: 17px;
    letter-spacing: 2.4px;
    color: var(--paper);
  }

  .person {
    position: absolute;
    right: 284px;
    top: 196px;
    text-align: right;
    font-size: 13px;
    line-height: 21px;
  }
  .person__name { font-size: 19px; font-weight: 700; line-height: 24px; margin-bottom: 2px; }
  .divider {
    position: absolute;
    left: 256px;
    top: 198px;
    width: 1px;
    height: 78px;
    background: var(--ink-light);
  }
  .contacts {
    position: absolute;
    left: 271px;
    top: 198px;
    list-style: none;
    font-size: 13px;
    line-height: 20px;
  }
  .contacts li { display: flex; align-items: center; gap: 6px; }
  .contacts svg { width: 10px; height: 10px; fill: var(--ink-light); flex: none; }
</style>
</head>
<body>

  <section class="card card--front" aria-label="Card front">
    <div class="wordmark wordmark--hero"><span class="wordmark__dot"></span>The Kestrel Works</div>
  </section>

  <section class="card card--contact" aria-label="Card back with contact details">
    <div class="wordmark wordmark--header"><span class="wordmark__dot"></span>The Kestrel Works</div>
    <div class="person">
      <p class="person__name">Your Name</p>
      <p>Title</p>
      <p>00, Complex name</p>
      <p>City, State 0042</p>
    </div>
    <span class="divider"></span>
    <ul class="contacts">
      <li><svg viewBox="0 0 10 10"><path d="M2 0.5 L3.6 2.6 L2.8 3.6 Q4 6 6.4 7.2 L7.4 6.4 L9.5 8 L8.3 9.5 Q1 8 0.5 1.7 Z"/></svg>0987 654321</li>
      <li><svg viewBox="0 0 10 10"><rect x="0.5" y="3.5" width="9" height="4.5" rx="1"/><path d="M2 3.5 Q2 1 5 1 Q8 1 8 3.5 Z"/></svg>0987 654321</li>
      <li><svg viewBox="0 0 10 10"><path d="M0.5 2 H9.5 V8.5 H0.5 Z M1.2 2.6 L5 5.6 L8.8 2.6 Z" fill-rule="evenodd"/></svg>info@kestrelworks.com</li>
      <li><svg viewBox="0 0 10 10"><circle cx="5" cy="5" r="4.5"/><path d="M0.5 5 H9.5 M5 0.5 V9.5" stroke="#2b2b2b" stroke-width="0.8"/></svg>www.kestrelworks.com</li>
    </ul>
  </section>

  <section class="card card--brand" aria-label="Card back with name and web address">
    <div class="wordmark wordmark--mid"><span class="wordmark__dot"></span>The Kestrel Works</div>
    <p class="web">www.kestrelworks.com</p>
  </section>

  <section class="card card--word" aria-label="Card back with name only">
    <div class="wordmark wordmark--large">The Kestrel Works</div>
    <p class="web">www.kestrelworks.com</p>
  </section>

</body>
</html>
```